Thornvale Group needs a business card design

We need a new business card design using the logo recently selected in a logo competition on Pixel Bazaar. Our business is a consultancy specializing in aviation and energy and the winning business card design will promote an image of precision and professionalism with creativity.

Please use the logo with the name on the front of the card and use a complementary font. Make the back white with either the light grey or dark grey logo.

Target Market(s)

Senior finance and legal leaders at aviation and energy companies

Industry/Entity Type

Management Consulting

Contact Information for Business Card

Peter Castrell
President
Thornvale Group

www.thornvalegroup.example

(555) 204-6391
pc@thornvalegroup.example

Requirements
Must have
• Professional font that goes well with the logo font

```html
<!DOCTYPE html>
<html lang="en">
<head>
<meta charset="utf-8">
<title>Thornvale Group – Business Card</title>
<link rel="stylesheet" href="https://fonts.googleapis.com/css2?family=Nunito+Sans:wght@300;400&display=swap">
<style>
  :root {
    --backdrop: #9c9c9c;
    --card: #eef0f2;
    --navy: #0e3560;
    --ink: #2e3540;
    --muted: #7a7f86;
    --body-font: "Nunito Sans", sans-serif;
  }
  * { margin: 0; padding: 0; box-sizing: border-box; }
  html, body {
    width: 1105px;
    height: 1200px;
    overflow: hidden;
    background: var(--backdrop);
    font-family: var(--body-font);
  }
  .canvas { position: relative; width: 1105px; height: 1200px; }
  .card {
    position: absolute;
    left: 182px;
    width: 746px;
    height: 428px;
    background: var(--card);
    overflow: hidden;
  }
  .card--front { top: 119px; }
  .card--back { top: 635px; }

  .accent-band {
    position: absolute;
    left: 0; top: 0;
    width: 34px; height: 100%;
    background: var(--navy);
  }

  .front-details {
    position: absolute;
    right: 38px;
    top: 34px;
    text-align: right;
  }
  .brand-name {
    font-weight: 300;
    color: var(--navy);
    font-size: 34px;
    letter-spacing: 3px;
    text-transform: uppercase;
    line-height: 1;
  }
  .person-name {
    margin-top: 52px;
    font-weight: 400;
    color: var(--navy);
    font-size: 27px;
    letter-spacing: 1px;
    text-transform: uppercase;
    line-height: 1.1;
  }
  .person-title {
    font-weight: 300;
    color: var(--muted);
    font-size: 19px;
    line-height: 1.3;
  }
  .company-lines {
    margin-top: 12px;
    font-weight: 300;
    color: var(--ink);
    font-size: 20px;
    line-height: 29px;
  }
  .contact-list {
    list-style: none;
    margin-top: 12px;
    font-weight: 300;
    color: var(--ink);
    font-size: 20px;
    line-height: 31px;
  }
  .contact-list li {
    display: flex;
    justify-content: flex-end;
    align-items: center;
    gap: 10px;
  }
  .contact-icon { width: 17px; height: 17px; fill: var(--navy); flex: none; }

  .back-brand {
    position: absolute;
    left: 0; right: 0;
    top: 150px;
    display: flex;
    flex-direction: column;
    align-items: center;
    gap: 34px;
  }
  .brand-square { width: 40px; height: 40px; background: var(--navy); }
  .back-brand .brand-name { font-size: 38px; letter-spacing: 4px; }
</style>
</head>
<body>
<main class="canvas">
  <section class="card card--front" aria-label="Card front">
    <div class="accent-band"></div>
    <div class="front-details">
      <p class="brand-name">Thornvale Group</p>
      <p class="person-name">Peter Castrell</p>
      <p class="person-title">President</p>
      <div class="company-lines">
        <p>Thornvale Group LLC</p>
        <p>Finance and Strategy Consulting</p>
        <p>Aviation - Manufacturing - Energy</p>
      </div>
      <ul class="contact-list">
        <li>(555) 204-6391
          <svg class="contact-icon" viewBox="0 0 24 24" aria-hidden="true"><path d="M6.6 10.8a15.1 15.1 0 0 0 6.6 6.6l2.2-2.2a1 1 0 0 1 1-.25 11.4 11.4 0 0 0 3.6.57 1 1 0 0 1 1 1V20a1 1 0 0 1-1 1A17 17 0 0 1 3 4a1 1 0 0 1 1-1h3.5a1 1 0 0 1 1 1c0 1.25.2 2.45.57 3.6a1 1 0 0 1-.25 1z"/></svg>
        </li>
        <li>pc@thornvalegroup.example
          <svg class="contact-icon" viewBox="0 0 24 24" aria-hidden="true"><path d="M2 5h20v14H2z M3.5 6.5 12 12.5l8.5-6" fill="var(--navy)"/><path d="M3 6.5 12 13l9-6.5" fill="none" stroke="var(--card)" stroke-width="1.6"/></svg>
        </li>
        <li>www.thornvalegroup.example
          <svg class="contact-icon" viewBox="0 0 24 24" aria-hidden="true"><circle cx="12" cy="12" r="10"/><path d="M2 12h20M12 2c3 3 3 17 0 20M12 2c-3 3-3 17 0 20" fill="none" stroke="var(--card)" stroke-width="1.4"/></svg>
        </li>
      </ul>
    </div>
  </section>

  <section class="card card--back" aria-label="Card back">
    <div class="back-brand">
      <div class="brand-square"></div>
      <p class="brand-name">Thornvale Group</p>
    </div>
  </section>
</main>
</body>
</html>
```